SkyvornQ Business Cards and Stationary Design

Need a design for our business cards and stationary. I want to carry on the theme of the logo. I want the business cards to have a design on the back. I would like the business cards and the stationary to carry the same theme, design scheme, and branding

Target Market(s)

Airlines and Maintenance Facilities

Industry/Entity Type

Aviation

Contact Information for Business Card

Name
Position Title
Address: 4827 Trellis Hollow Road, Fort Pierce, Florida, 34951
Office Number
Mobile Number
Email
Website

Font styles to use
Serif
Sans Serif

Colors

Designer to choose colors to be used in the design.

```html
<!DOCTYPE html>
<html lang="en">
<head>
<meta charset="utf-8">
<title>SkyvornQ Business Card</title>
<link href="https://fonts.googleapis.com/css2?family=Montserrat:wght@400;500;600;800&display=swap" rel="stylesheet">
<style>
  :root {
    --page: #e9ecf1;
    --navy: #163463;
    --navy-deep: #0f2750;
    --navy-light: #1d3f73;
    --sky: #2fb0e3;
    --sky-dark: #239bcc;
    --white: #ffffff;
    --soft: #cfe0f3;
  }
  * { box-sizing: border-box; margin: 0; padding: 0; }
  html, body { width: 1200px; height: 800px; overflow: hidden; }
  body {
    background: var(--page);
    font-family: "Montserrat", sans-serif;
    color: var(--white);
    position: relative;
  }
  .card {
    position: absolute;
    width: 560px;
    height: 320px;
    border-radius: 14px;
    overflow: hidden;
    box-shadow: 0 14px 30px rgba(15, 39, 80, 0.28);
  }

  /* Front */
  .card-front { left: 60px; top: 60px; }
  .front-backdrop {
    position: absolute; inset: 0;
    background: radial-gradient(ellipse at 45% 45%, var(--navy-light), var(--navy-deep));
  }
  .front-brand {
    position: absolute; left: 0; right: 0; top: 92px;
    display: flex; align-items: center; justify-content: center; gap: 18px;
  }
  .brand-dot {
    width: 58px; height: 58px; border-radius: 50%;
    border: 6px solid var(--white);
  }
  .brand-name {
    font-weight: 800; letter-spacing: 6px; text-transform: uppercase;
    color: var(--white);
  }
  .front-brand .brand-name { font-size: 42px; }
  .front-address {
    position: absolute; left: 0; right: 0; top: 232px;
    text-align: center; font-size: 13px; font-weight: 500; letter-spacing: 0.3px;
  }

  /* Back */
  .card-back {
    left: 580px; top: 420px;
    background: linear-gradient(135deg, var(--navy-light), var(--navy-deep));
  }
  .back-brand {
    position: absolute; left: 34px; top: 128px; width: 250px;
    display: flex; flex-direction: column; align-items: center; gap: 12px;
  }
  .back-brand .brand-dot { width: 46px; height: 46px; border-width: 5px; }
  .back-brand .brand-name { font-size: 26px; letter-spacing: 4px; }
  .band-tab {
    position: absolute; left: 300px; top: 0; width: 50px; height: 70px;
    background: var(--sky); border-radius: 0 0 25px 25px;
  }
  .band-icons {
    position: absolute; left: 300px; top: 100px; bottom: 0; width: 50px;
    background: var(--sky); border-radius: 25px 25px 0 0;
    display: flex; flex-direction: column; align-items: center;
    padding-top: 24px;
  }
  .band-icons svg {
    width: 22px; height: 22px; margin-bottom: 25px;
    fill: none; stroke: var(--white); stroke-width: 1.8;
    stroke-linecap: round; stroke-linejoin: round;
  }
  .holder {
    position: absolute; left: 372px; top: 20px;
  }
  .holder-name { font-size: 24px; font-weight: 600; letter-spacing: 1px; text-transform: uppercase; }
  .holder-role { font-size: 13px; font-weight: 400; color: var(--soft); margin-top: 2px; }
  .contact-list {
    position: absolute; left: 372px; top: 126px; list-style: none;
  }
  .contact-list li {
    font-size: 14px; font-weight: 500; height: 47px; line-height: 20px;
  }
</style>
</head>
<body>

  <section class="card card-front" aria-label="Business card front">
    <div class="front-backdrop" role="img" aria-label="Navy background with faint repeating brand pattern"></div>
    <div class="front-brand">
      <span class="brand-dot"></span>
      <span class="brand-name">SkyvornQ</span>
    </div>
    <p class="front-address">4827 Trellis Hollow Road, Fort Pierce, Florida, 34951</p>
  </section>

  <section class="card card-back" aria-label="Business card back">
    <div class="back-brand">
      <span class="brand-dot"></span>
      <span class="brand-name">SkyvornQ</span>
    </div>

    <div class="band-tab"></div>
    <div class="band-icons">
      <svg viewBox="0 0 24 24" aria-label="Mobile"><rect x="7" y="2.5" width="10" height="19" rx="2"/><line x1="11" y1="18" x2="13" y2="18"/></svg>
      <svg viewBox="0 0 24 24" aria-label="Office phone"><path d="M5 3h4l2 5-2.5 1.5a11 11 0 0 0 6 6L16 13l5 2v4a2 2 0 0 1-2 2A16 16 0 0 1 3 5a2 2 0 0 1 2-2z"/></svg>
      <svg viewBox="0 0 24 24" aria-label="Email"><rect x="3" y="5.5" width="18" height="13" rx="1.5"/><polyline points="3.5,6.5 12,13 20.5,6.5"/></svg>
      <svg viewBox="0 0 24 24" aria-label="Website"><circle cx="12" cy="12" r="9"/><ellipse cx="12" cy="12" rx="4" ry="9"/><line x1="3" y1="12" x2="21" y2="12"/><line x1="5" y1="7" x2="19" y2="7"/><line x1="5" y1="17" x2="19" y2="17"/></svg>
    </div>

    <div class="holder">
      <p class="holder-name">Dana Merrow</p>
      <p class="holder-role">CEO/ Founder</p>
    </div>

    <ul class="contact-list">
      <li>(555) 318-4072</li>
      <li>1-800-555-0147</li>
      <li>info@skyvornq.com</li>
      <li>www.skyvornq.com</li>
    </ul>
  </section>

</body>
</html>
```